Brisk Harbor claims recovery services

Its a new company in Dubai UAE. The company activity is debt management, debt collection, loans settlements and restructuring. The company involved in any business or sector requires debt management including government entities, Medical & Health care sector, Banks & finance companies, SME's and commercial business.

Target Market(s)

government entities, Medical & Health care sector, Banks & finance companies, SME's and commercial business.

Industry/Entity Type

Financial Service

Number of Pages Required

5+ page

Requirements
Must have
• Focus on the services not the team and clients
Should not have
• Colorful . Shouldn't have Client testimonial and our clients

```html
<!DOCTYPE html>
<html lang="en">
<head>
<meta charset="utf-8">
<title>Brisk Harbor – Claims Recovery Services</title>
<link rel="stylesheet" href="https://fonts.googleapis.com/css2?family=Cinzel:wght@400;700&family=Arimo:wght@400;700&display=swap">
<style>
  :root{
    --brand-blue:#2c5f8b;
    --brand-blue-dark:#234d72;
    --accent-red:#e2393f;
    --ink:#1d1d1d;
    --body-text:#555;
    --light-bg:#f4f4f4;
    --contact-bg:#f2f2f2;
    --field-border:#cfd4d9;
    --sector-bg:#e4ebf2;
    --white:#fff;
  }
  *{box-sizing:border-box;margin:0;padding:0}
  html,body{width:1200px;height:2740px;overflow:hidden}
  body{position:relative;background:var(--white);font-family:"Arimo",Arial,sans-serif;color:var(--body-text)}
  a{text-decoration:none}

  /* navigation */
  .site-nav{position:absolute;left:0;top:0;width:1200px;height:62px;background:var(--brand-blue);display:flex;justify-content:center;align-items:center;gap:26px}
  .site-nav a{color:#dce6ef;font-family:"Cinzel",Georgia,serif;font-size:16px;letter-spacing:.5px}
  .site-nav a.active{color:var(--white);font-weight:700}
  .site-nav .sep{width:7px;height:7px;background:var(--white);transform:rotate(45deg)}

  /* hero */
  .hero{position:absolute;left:0;top:62px;width:1200px;height:620px;overflow:hidden}
  .hero-photo{position:absolute;inset:0;background:linear-gradient(180deg,#6f9fd0 0%,#b9d2ea 30%,#dfe7ee 45%,#8ca2a8 62%,#6f8780 80%,#9aa89a 100%)}
  .hero-curve{position:absolute;left:0;bottom:0}
  .brand{position:absolute;left:0;width:1200px;text-align:center}
  .brand-dot{top:120px;left:570px;width:60px;height:60px;border-radius:50%;background:var(--brand-blue)}
  .brand-name{top:218px;font-family:"Cinzel",Georgia,serif;font-size:44px;color:var(--brand-blue);letter-spacing:1px}
  .brand-tag{top:276px;display:flex;justify-content:center;align-items:center;gap:12px;font-family:"Cinzel",Georgia,serif;font-size:12px;letter-spacing:3px;color:#1f3f5c}
  .brand-tag i{display:block;width:60px;height:1px;background:#1f3f5c}

  /* welcome */
  .welcome{position:absolute;left:0;top:682px;width:1200px;height:340px;background:var(--light-bg);text-align:center}
  .welcome h1{position:absolute;top:40px;width:100%;font-family:"Cinzel",Georgia,serif;font-weight:400;font-size:46px;color:var(--ink);letter-spacing:1px}
  .welcome h1 span,.promise h2 span,.sectors h2 span{color:var(--brand-blue)}
  .welcome .tagline{position:absolute;top:94px;width:100%;display:flex;justify-content:center;align-items:center;gap:14px;font-family:"Cinzel",Georgia,serif;font-size:19px;letter-spacing:5px;color:#444}
  .welcome .tagline i{display:block;width:60px;height:2px;background:#666}
  .welcome .copy{position:absolute;top:138px;left:130px;width:940px;font-size:14px;line-height:17px;color:#555}
  .welcome .copy p{margin-bottom:13px}
  .btn{display:inline-block;background:var(--brand-blue);color:var(--white);font-size:16px;text-transform:uppercase;border-radius:3px;text-decoration:none}
  .welcome .btn{position:absolute;top:288px;left:527px;width:146px;height:50px;line-height:50px}

  /* services */
  .services{position:absolute;left:0;top:1022px;width:1200px;height:415px;overflow:hidden}
  .services-photo{position:absolute;inset:0;background:linear-gradient(180deg,#3a3f46 0%,#2d5a82 35%,#3a6890 65%,#2c5880 100%)}
  .services .band{position:absolute;left:0;top:0}
  .service{position:absolute;top:0;width:600px;height:415px;text-align:center;color:var(--white)}
  .service-word{position:absolute;top:58px;width:100%;font-size:82px;font-weight:700;letter-spacing:-1px}
  .service .service-icon{position:absolute;top:196px;left:272px}
  .service h3{position:absolute;top:268px;width:100%;font-family:"Cinzel",Georgia,serif;font-weight:400;font-size:33px;letter-spacing:1px}
  .service p{position:absolute;top:324px;left:125px;width:350px;font-size:14px;line-height:22px;color:#e6eef5}

  /* promise */
  .promise{position:absolute;left:0;top:1437px;width:1200px;height:417px;background:var(--white)}
  .promise-photo{position:absolute;left:0;top:0;width:560px;height:417px;background:linear-gradient(90deg,#c9cfd5 0%,#e6e9ec 60%,#fff 100%)}
  .promise .mini-brand{position:absolute;top:90px;left:630px;width:500px;text-align:center;font-family:"Cinzel",Georgia,serif;font-size:18px;color:var(--brand-blue)}
  .promise h2{position:absolute;top:150px;left:600px;width:560px;text-align:center;font-family:"Cinzel",Georgia,serif;font-weight:400;font-size:46px;color:var(--ink)}
  .promise p{position:absolute;top:216px;left:625px;width:510px;text-align:center;font-size:16px;line-height:24px;color:#555}

  /* sectors */
  .sectors{position:absolute;left:0;top:1854px;width:1200px;height:479px;background:var(--white)}
  .sectors h2{position:absolute;top:40px;width:100%;text-align:center;font-family:"Cinzel",Georgia,serif;font-weight:400;font-size:44px;color:var(--ink)}
  .sector{position:absolute;top:126px;width:340px;text-align:center}
  .sector-badge{position:relative;margin:0 auto;width:146px;height:146px;border-radius:50%;background:var(--sector-bg);display:flex;align-items:center;justify-content:center}
  .sector-dot{position:absolute;right:-8px;bottom:4px;width:42px;height:42px;border-radius:50%;background:var(--brand-blue);border:3px solid var(--white)}
  .sector p{margin-top:30px;font-size:14px;line-height:23px;color:#555}
  .sector h3{margin-top:14px;font-weight:400;font-family:"Cinzel",Georgia,serif;font-size:20px;color:var(--brand-blue);letter-spacing:1px}

  /* contact */
  .contact{position:absolute;left:0;top:2333px;width:1200px;height:356px;background:var(--contact-bg)}
  .contact h4{position:absolute;top:50px;font-family:"Cinzel",Georgia,serif;font-weight:400;font-size:23px;color:var(--ink);letter-spacing:1.5px}
  .field{position:absolute;background:var(--white);border:1px solid var(--field-border);border-radius:3px;font-size:14px;color:#555;padding:16px 22px}
  .submit{position:absolute;left:555px;top:105px;width:187px;height:50px;line-height:50px;text-align:center;font-size:20px;letter-spacing:1px}
  .detail{position:absolute;left:800px;display:flex;align-items:flex-start;gap:14px;font-size:14px;color:#555}
  .detail svg{flex:none}
  .detail .co{font-family:"Cinzel",Georgia,serif;font-size:18px;color:var(--brand-blue);display:block;margin-bottom:4px}
  .social{position:absolute;top:271px;left:800px;display:flex;gap:11px}
  .social span{width:42px;height:42px;border:1px solid #bfc6cd;background:#e8ebee;border-radius:2px}
  .social span.primary{background:var(--brand-blue);border-color:var(--brand-blue)}

  /* footer */
  .site-footer{position:absolute;left:0;top:2689px;width:1200px;height:51px;background:var(--brand-blue);color:var(--white);text-align:center;line-height:51px;font-family:"Cinzel",Georgia,serif;font-size:14px;letter-spacing:1px}
</style>
</head>
<body>

<nav class="site-nav">
  <a class="active" href="#">HOME</a><i class="sep"></i>
  <a href="#">ABOUT</a><i class="sep"></i>
  <a href="#">SERVICES</a><i class="sep"></i>
  <a href="#">SECTORS</a><i class="sep"></i>
  <a href="#">CONTACT</a>
</nav>

<header class="hero">
  <div class="hero-photo" role="img" aria-label="Aerial view of a waterfront city skyline under a cloudy blue sky"></div>
  <div class="brand brand-dot"></div>
  <div class="brand brand-name">BRISK HARBOR</div>
  <div class="brand brand-tag"><i></i>CLAIMS RECOVERY SERVICES<i></i></div>
  <svg class="hero-curve" width="1200" height="70" viewBox="0 0 1200 70">
    <path d="M0 2 Q600 92 1200 2 L1200 70 L0 70 Z" fill="#f4f4f4"/>
  </svg>
</header>

<section class="welcome">
  <h1>WELCOME TO <span>BRISK HARBOR</span></h1>
  <div class="tagline"><i></i>CLAIMS RECOVERY SERVICES<i></i></div>
  <div class="copy">
    <p>We are a Claims Recovery and Debt Management Services company based in Dubai, United Arab Emirates. The Brisk Harbor team handles a comprehensive range of debt recoveries, such as invoices; insurance payments; supplier and rent payments; and personal and business loans, for individuals and businesses across an array of industries.</p>
    <p>Brisk Harbor was founded on traditional values, and we're proud of our personal approach. Our people are experienced, effective and efficient, but never compromise on providing a client-focused service.</p>
    <p>Read more about our services, or contact us to find out how we can help.</p>
  </div>
  <a class="btn" href="#">Read More</a>
</section>

<section class="services">
  <div class="services-photo" role="img" aria-label="Businessman in a dark suit standing with hands clasped"></div>
  <svg class="band" width="1200" height="415" viewBox="0 0 1200 415">
    <polygon points="0,0 1200,0 1200,40 600,72 0,40" fill="#3b3f45" opacity=".85"/>
    <polygon points="0,42 600,74 1200,42 1200,161 0,161" fill="#e2393f"/>
    <polygon points="600,74 1200,42 1200,161 600,161" fill="#e84448" opacity=".6"/>
    <rect x="0" y="161" width="1200" height="254" fill="#2c5f8b" opacity=".55"/>
    <line x1="600" y1="40" x2="600" y2="415" stroke="#ffffff" stroke-opacity=".45" stroke-width="2"/>
  </svg>
  <div class="service" style="left:0">
    <div class="service-word">Claims</div>
    <svg class="service-icon" width="52" height="56" viewBox="0 0 52 56" fill="none" stroke="#fff" stroke-width="2.5">
      <rect x="6" y="3" width="32" height="44" rx="2"/>
      <rect x="14" y="9" width="32" height="44" rx="2" fill="#2f5e86"/>
      <line x1="20" y1="20" x2="40" y2="20"/><line x1="20" y1="28" x2="40" y2="28"/><line x1="20" y1="36" x2="34" y2="36"/>
    </svg>
    <h3>CLAIMS RECOVERY</h3>
    <p>Lorem Ipsum is simply dummy text of the printing and typesetting industry. Lorem Ipsum has</p>
  </div>
  <div class="service" style="left:600px">
    <div class="service-word">Debt</div>
    <svg class="service-icon" width="56" height="56" viewBox="0 0 56 56" fill="none" stroke="#fff" stroke-width="2.5">
      <line x1="28" y1="6" x2="28" y2="48"/><line x1="8" y1="14" x2="48" y2="14"/>
      <line x1="16" y1="48" x2="40" y2="48"/>
      <path d="M8 14 L2 30 H14 Z"/><path d="M48 14 L42 30 H54 Z"/>
    </svg>
    <h3>DEBT MANAGEMENT</h3>
    <p>Lorem Ipsum is simply dummy text of the printing and typesetting industry. Lorem Ipsum has</p>
  </div>
</section>

<section class="promise">
  <div class="promise-photo" role="img" aria-label="Three colleagues gathered around a laptop in a bright office"></div>
  <div class="mini-brand">BRISK HARBOR</div>
  <h2>OUR <span>PROMISE</span> TO YOU</h2>
  <p>Brisk Harbor understands that debt, whether you're owed or owing, brings with it stress and worry. We promise to work tirelessly to alleviate some of that stress. We promise complete honesty, transparency and discretion. And we promise that our fees are always fair.</p>
</section>

<section class="sectors">
  <h2>SECTORS WE <span>SERVE</span></h2>
  <article class="sector" style="left:75px">
    <div class="sector-badge">
      <svg width="56" height="56" viewBox="0 0 56 56" fill="none" stroke="#2c5f8b" stroke-width="2.5"><path d="M6 20 L28 8 L50 20 Z"/><line x1="14" y1="24" x2="14" y2="42"/><line x1="24" y1="24" x2="24" y2="42"/><line x1="32" y1="24" x2="32" y2="42"/><line x1="42" y1="24" x2="42" y2="42"/><line x1="6" y1="47" x2="50" y2="47"/></svg>
      <span class="sector-dot"></span>
    </div>
    <p>Recovery of fees, levies and outstanding dues for public bodies, handled with full discretion, clear reporting and strict compliance at every stage of the process.</p>
    <h3>GOVERNMENT</h3>
  </article>
  <article class="sector" style="left:431px">
    <div class="sector-badge">
      <svg width="56" height="56" viewBox="0 0 56 56" fill="none" stroke="#2c5f8b" stroke-width="2.5"><rect x="8" y="8" width="40" height="40" rx="4"/><line x1="28" y1="17" x2="28" y2="39"/><line x1="17" y1="28" x2="39" y2="28"/></svg>
      <span class="sector-dot"></span>
    </div>
    <p>Settlement of patient balances and insurance claims for hospitals and clinics, so medical teams can stay focused on care while we manage the follow-up.</p>
    <h3>HEALTHCARE</h3>
  </article>
  <article class="sector" style="left:787px">
    <div class="sector-badge">
      <svg width="56" height="56" viewBox="0 0 56 56" fill="none" stroke="#2c5f8b" stroke-width="2.5"><rect x="6" y="14" width="44" height="30" rx="3"/><line x1="6" y1="22" x2="50" y2="22"/><line x1="12" y1="34" x2="24" y2="34"/></svg>
      <span class="sector-dot"></span>
    </div>
    <p>Loan settlements and debt restructuring for banks, finance companies, SMEs and commercial businesses, with plans built around each portfolio.</p>
    <h3>BANKS &amp; BUSINESS</h3>
  </article>
</section>

<section class="contact">
  <h4 style="left:80px">KEEP IN TOUCH WITH US</h4>
  <div class="field" style="left:77px;top:105px;width:228px;height:50px">Name:</div>
  <div class="field" style="left:316px;top:105px;width:228px;height:50px">Subject:</div>
  <a class="btn submit" href="#">Submit</a>
  <div class="field" style="left:77px;top:169px;width:228px;height:50px">Phone:</div>
  <div class="field" style="left:316px;top:169px;width:426px;height:50px">E-Mail:</div>
  <div class="field" style="left:77px;top:231px;width:665px;height:79px">Message:</div>

  <h4 style="left:791px">CONTACT DETAILS</h4>
  <div class="detail" style="top:100px">
    <svg width="22" height="28" viewBox="0 0 22 28" fill="none" stroke="#555" stroke-width="1.8"><path d="M11 26 C4 17 2 13 2 10 a9 9 0 0 1 18 0 c0 3 -2 7 -9 16Z"/><circle cx="11" cy="10" r="3.5"/></svg>
    <div><span class="co">BRISK HARBOR</span>P.O. Box 123-456, City, Country</div>
  </div>
  <div class="detail" style="top:160px">
    <svg width="22" height="22" viewBox="0 0 22 22" fill="none" stroke="#555" stroke-width="1.8"><path d="M4 2 L8 2 L10 7 L7 9 C8 12 10 14 13 15 L15 12 L20 14 L20 18 C20 19 19 20 18 20 C9 20 2 13 2 4 C2 3 3 2 4 2Z"/></svg>
    <div>123 4567 890</div>
  </div>
  <div class="detail" style="top:196px">
    <svg width="22" height="22" viewBox="0 0 22 22" fill="none" stroke="#555" stroke-width="1.8"><rect x="5" y="2" width="12" height="6"/><rect x="2" y="8" width="18" height="9" rx="1"/><rect x="5" y="14" width="12" height="6"/></svg>
    <div>123 4567 890</div>
  </div>
  <div class="detail" style="top:232px">
    <svg width="22" height="18" viewBox="0 0 22 18" fill="none" stroke="#555" stroke-width="1.8"><rect x="1.5" y="2" width="19" height="14" rx="1"/><path d="M2 3 L11 10 L20 3"/></svg>
    <div>info@briskharbor.com</div>
  </div>
  <div class="social"><span class="primary"></span><span></span><span></span><span></span></div>
</section>

<footer class="site-footer">© BRISK HARBOR - 2016. ALL RIGHTS RESERVED</footer>

</body>
</html>
```